BRIGHT RIVER POWER.

I'd like my business logo.
contact name: Dennis Halvorsen
phone:0438759164
email: info@brightriverpower.net.au
website: www.brightriverpower.net.au

services:
solar
battery storage
LED lighting
energy saving solutions
general electrical
I'd like the design to look professional

Target Market(s)

Everyone

Industry/Entity Type

Business

Contact Information for Business Card

as described above

Requirements
Must have
• Id like the colours and the design to work well with my logo.

```html
<!DOCTYPE html>
<html lang="en">
<head>
<meta charset="utf-8">
<title>Bright River Power – Business Card</title>
<link rel="stylesheet" href="https://fonts.googleapis.com/css2?family=Source+Sans+3:wght@400;600;700&display=swap">
<style>
  :root {
    --backdrop: #000000;
    --card: #2f3032;
    --card-edge: #38393b;
    --divider: #3f4042;
    --orange: #f29a17;
    --green: #8cc63f;
    --green-dark: #5fa32a;
  }
  * { margin: 0; padding: 0; box-sizing: border-box; }
  html, body { width: 1200px; height: 900px; overflow: hidden; background: var(--backdrop); }
  body { position: relative; font-family: "Source Sans 3", sans-serif; }

  .card {
    position: absolute;
    width: 457px; height: 281px;
    border-radius: 14px;
    background: radial-gradient(ellipse at 50% 40%, var(--card-edge), var(--card) 70%);
  }
  .card--front { left: 137px; top: 271px; }
  .card--back  { left: 626px; top: 271px; }

  .divider {
    position: absolute;
    top: 78px; width: 1px; height: 124px;
    background: var(--divider);
  }
  .card--front .divider { left: 222px; }
  .card--back  .divider { left: 235px; }

  /* brand name in place of the mark */
  .brand {
    position: absolute;
    display: flex; align-items: center; gap: 10px;
    color: var(--green);
    font-weight: 700;
    line-height: 1.05;
    text-transform: uppercase;
  }
  .brand__dot {
    width: 18px; height: 18px; border-radius: 50%;
    background: var(--orange); flex: none;
  }
  .card--front .brand { left: 48px; top: 108px; font-size: 22px; }
  .card--back .brand { left: 38px; top: 102px; font-size: 24px; }

  .contact { position: absolute; left: 242px; top: 90px; }
  .contact__name {
    color: var(--orange); font-size: 17px; font-weight: 600;
    margin-bottom: 22px;
  }
  .contact__list { list-style: none; }
  .contact__item {
    display: flex; align-items: center; gap: 7px;
    color: var(--green); font-size: 13px; height: 19px;
  }
  .contact__icon { width: 10px; height: 10px; flex: none; fill: var(--orange); }

  .services { position: absolute; left: 252px; top: 78px; }
  .services__title {
    color: var(--orange); font-size: 24px; font-weight: 600;
    margin-bottom: 8px;
  }
  .services__list { list-style: none; }
  .services__item {
    display: flex; align-items: center; gap: 7px;
    color: var(--green); font-size: 13px; font-weight: 600; height: 19px;
  }
  .services__bullet {
    width: 10px; height: 10px; border-radius: 50%;
    background: var(--green-dark); flex: none;
  }
</style>
</head>
<body>

<section class="card card--front">
  <div class="brand"><span class="brand__dot"></span><span>Bright<br>River<br>Power</span></div>
  <div class="divider"></div>
  <div class="contact">
    <p class="contact__name">Dennis Halvorsen</p>
    <ul class="contact__list">
      <li class="contact__item">
        <svg class="contact__icon" viewBox="0 0 10 10"><path d="M2 0.5 L3.6 2.6 L2.7 3.6 C3.3 5 4.8 6.6 6.4 7.3 L7.4 6.4 L9.5 8 L8.4 9.5 C4.5 9.2 0.8 5.5 0.5 1.6 Z"/></svg>
        <span>0438759164</span>
      </li>
      <li class="contact__item">
        <svg class="contact__icon" viewBox="0 0 10 10"><rect x="0.5" y="2" width="9" height="6.5"/><path d="M0.5 2 L5 5.5 L9.5 2" fill="none" stroke="#2f3032" stroke-width="1"/></svg>
        <span>info@brightriverpower.net.au</span>
      </li>
      <li class="contact__item">
        <svg class="contact__icon" viewBox="0 0 10 10"><circle cx="5" cy="5" r="4.5"/><path d="M0.5 5 H9.5 M5 0.5 C2.8 3 2.8 7 5 9.5 M5 0.5 C7.2 3 7.2 7 5 9.5" fill="none" stroke="#2f3032" stroke-width="0.8"/></svg>
        <span>www.brightriverpower.net.au</span>
      </li>
    </ul>
  </div>
</section>

<section class="card card--back">
  <div class="brand"><span class="brand__dot"></span><span>Bright<br>River<br>Power</span></div>
  <div class="divider"></div>
  <div class="services">
    <h2 class="services__title">What I do</h2>
    <ul class="services__list">
      <li class="services__item"><span class="services__bullet"></span>Solar</li>
      <li class="services__item"><span class="services__bullet"></span>Battery Storage</li>
      <li class="services__item"><span class="services__bullet"></span>LED Lighting</li>
      <li class="services__item"><span class="services__bullet"></span>Energy Saving Solutions</li>
    </ul>
  </div>
</section>

</body>
</html>
```